KTWG application splash screen

We need a 1024x768 image for use as an application splash screen.
The image will be displayed full screen on an 10 inch industrial PC 1024x768 screen while our application is launching. The image should convey that the application is "Waiting for connection to Wi-Fi access point..." and include a graphic of the industrial PC connected to the access point via an Ethernet cable. A list of troubleshooting steps should be included at the bottom of the image. The troubleshooting steps should not be the main focus of the image and should be shown in a smaller font (but still readable at 1024x768 displayed on a 10 inch screen).
I will include a mock up of the general idea of what we are looking for as well as image files for the industrial PC, a screenshot of our application to show on the PC's screen and the AP.
For general look and feel and a sense of corporate branding please review our website https://marrowgatesoilworks.example/. The splash screen should reflect corporate branding.
Target Market(s)
Users of our application
Industry/Entity Type
Agriculture
Look and feel

```html
<!DOCTYPE html>
<html lang="en">
<head>
<meta charset="utf-8">
<title>KTWG – Waiting for Wi-Fi connection</title>
<link rel="stylesheet" href="https://fonts.googleapis.com/css2?family=Poppins:wght@400;600;700&display=swap">
<style>
  :root {
    --brand-green: #2fb36c;
    --ink: #222222;
    --ink-soft: #3c3c3c;
    --body-text: #4a4a4a;
    --bg-light: #ffffff;
    --bg-shade: #d4d4d4;
    --device-dark: #1f1f1f;
    --device-screen: #dfe6e2;
    --ap-white: #f3f3f3;
  }
  * { margin: 0; padding: 0; box-sizing: border-box; }
  html, body { width: 1200px; height: 928px; overflow: hidden; }
  body {
    font-family: "Poppins", sans-serif;
    color: var(--ink);
  }
  .splash {
    position: relative;
    width: 1200px;
    height: 928px;
    background: linear-gradient(125deg, var(--bg-light) 0%, #f1f1f1 45%, var(--bg-shade) 100%);
    overflow: hidden;
  }
  .wifi-icon { position: absolute; left: 554px; top: 76px; width: 94px; height: 70px; }
  .status-title {
    position: absolute; left: 0; top: 152px; width: 1200px;
    text-align: center; font-weight: 400; font-size: 38px; line-height: 51px;
    color: var(--ink); letter-spacing: 0.5px;
  }
  .cab-computer {
    position: absolute; left: 125px; top: 303px; width: 338px; height: 277px;
    border-radius: 16px;
    background: linear-gradient(160deg, #3a3a3a, var(--device-dark));
  }
  .cab-computer .screen-area {
    position: absolute; left: 30px; top: 24px; width: 280px; height: 214px;
    background: linear-gradient(180deg, #f4f6f5, var(--device-screen));
    border-radius: 2px;
  }
  .cable { position: absolute; left: 0; top: 0; width: 1200px; height: 928px; }
  .access-point {
    position: absolute; left: 1040px; top: 298px; width: 29px; height: 226px;
    border-radius: 8px 8px 3px 3px;
    background: linear-gradient(90deg, #dcdcdc, var(--ap-white) 45%, #d0d0d0);
  }
  .access-point .status-light {
    position: absolute; left: 9px; top: 130px; width: 10px; height: 10px;
    border-radius: 50%; background: var(--brand-green);
  }
  .component-label {
    position: absolute; font-weight: 600; font-size: 18.5px; letter-spacing: 0.3px;
    color: var(--ink-soft); text-transform: uppercase; white-space: nowrap;
    transform: translateX(-50%);
  }
  .label-computer { left: 292px; top: 595px; }
  .label-cable { left: 585px; top: 562px; }
  .label-ap { left: 974px; top: 562px; }
  .troubleshooting { position: absolute; left: 168px; top: 657px; width: 1000px; }
  .troubleshooting-heading {
    display: flex; align-items: center; gap: 8px;
    font-weight: 700; font-size: 20.5px; color: var(--brand-green);
  }
  .troubleshooting-heading svg { width: 28px; height: 28px; }
  .steps { list-style: none; margin-top: 6px; }
  .steps li {
    position: relative; font-size: 15px; line-height: 26px; color: var(--body-text);
    padding-left: 54px;
  }
  .steps li::before {
    content: ""; position: absolute; left: 36px; top: 9px;
    width: 9px; height: 9px; border-radius: 50%; background: var(--ink);
  }
  .steps .sub-steps { list-style: none; margin-left: -54px; }
  .steps .sub-steps li { padding-left: 88px; line-height: 25.5px; }
  .steps .sub-steps li::before { left: 70px; }
  .brand-name {
    position: absolute; left: 983px; top: 812px;
    font-weight: 700; font-size: 32px; letter-spacing: 1px; color: var(--ink-soft);
  }
</style>
</head>
<body>
<main class="splash">
  <svg class="wifi-icon" viewBox="0 0 94 70" aria-hidden="true">
    <path d="M3 20 A62 62 0 0 1 91 20 L82 30 A49 49 0 0 0 12 30 Z" fill="var(--brand-green)"/>
    <path d="M18 36 A42 42 0 0 1 76 36 L67 46 A29 29 0 0 0 27 46 Z" fill="var(--brand-green)"/>
    <path d="M34 52 L47 68 L60 52 A19 19 0 0 0 34 52 Z" fill="var(--brand-green)"/>
  </svg>

  <h1 class="status-title">Waiting for connection to<br>Wi-Fi access point...</h1>

  <div class="cab-computer" role="img" aria-label="Industrial tractor cab computer showing the seeding application screen">
    <div class="screen-area"></div>
  </div>

  <svg class="cable" viewBox="0 0 1200 928" aria-hidden="true">
    <rect x="463" y="533" width="24" height="20" rx="3" fill="#2a2a2a"/>
    <rect x="485" y="537" width="14" height="12" rx="2" fill="#444"/>
    <path d="M498 543 H1044 Q1054 543 1054 533 V522" fill="none" stroke="#1e1e1e" stroke-width="4"/>
  </svg>

  <div class="access-point" role="img" aria-label="Outdoor Wi-Fi access point with green status light">
    <span class="status-light"></span>
  </div>

  <span class="component-label label-computer">Tractor Cab Computer</span>
  <span class="component-label label-cable">Ethernet Cable</span>
  <span class="component-label label-ap">Wi-Fi Access Point</span>

  <section class="troubleshooting">
    <h2 class="troubleshooting-heading">
      <svg viewBox="0 0 28 28" aria-hidden="true">
        <circle cx="14" cy="14" r="8" fill="none" stroke="var(--brand-green)" stroke-width="2"/>
        <circle cx="14" cy="14" r="3" fill="none" stroke="var(--brand-green)" stroke-width="2"/>
        <path d="M14 2v4M14 22v4M2 14h4M22 14h4M5.5 5.5l3 3M19.5 19.5l3 3M5.5 22.5l3-3M19.5 8.5l3-3" stroke="var(--brand-green)" stroke-width="2" stroke-linecap="round"/>
      </svg>
      Troubleshooting steps:
    </h2>
    <ul class="steps">
      <li>This screen should only be visible for a short time on boot.</li>
      <li>If this screen stays visible for more than a minute:
        <ul class="sub-steps">
          <li>Verify that the Wi-Fi Access Point (AP) powers up when this system does (indicated by a green light on the side of the AP).</li>
          <li>Check the Ethernet cable between this system and the AP for damage, and replace it if necessary.</li>
          <li>Power-cycle this system and wait for it to reboot fully.</li>
          <li>If the issue persists, contact KTWG support for further assistance.</li>
        </ul>
      </li>
    </ul>
  </section>

  <div class="brand-name">KTWG</div>
</main>
</body>
</html>
```